Design for Card Attached to Clothes

We sell rhythmic gymnastics apparel and are looking for someone create a card that will be attached to the products. You can see an example of the exact type of apparel in the files, as well as the current card that is attached to it. The design should have space on the top back for the sticker that has UPC and SKU information, as shown in the image attached.
- We would like the front to have our logo
- We would like the image of the girls added on the back
- Would be cool to see the gradient change to the white space on the back where the sticker will go but not required.
-The final card size is 10cm by 6cm, Their should be 2mm loss accounted for cutting the cards within the design. (meaning the design needs to be bigger than 10cm by 6cm to account for printing and cut)
- And the hole size that is at the top center is 3mm in diameter
- Name should be under logo
Access all logo files here https://files.varnolo.net/share/folders/7Kq2mzPtwR4xLbN9cVdHj3sYe81AfoGu?access=open
- Front will have logo
- Back will have image of girls and some creative design that you will create.
Target Market(s)
Females
Industry/Entity Type
Rhythmic Gymnastics

```html
<!DOCTYPE html>
<html lang="en">
<head>
<meta charset="utf-8">
<title>Velora Hang Tag – Front and Back</title>
<link rel="stylesheet" href="https://fonts.googleapis.com/css2?family=Quicksand:wght@500&display=swap">
<style>
  :root {
    --backdrop: #c6c5c6;
    --card: #ffffff;
    --hole: #c6c5c6;
    --magenta: #e4006d;
    --plum: #a0268a;
    --rose-soft: #f6c9dc;
    --photo-dark: #2a2a2a;
    --photo-mid: #5a4a4f;
  }
  html, body {
    margin: 0;
    padding: 0;
    width: 1200px;
    height: 987px;
    overflow: hidden;
    background: var(--backdrop);
  }
  .sheet {
    position: relative;
    width: 1200px;
    height: 987px;
  }
  .tag {
    position: absolute;
    top: 92px;
    width: 482px;
    height: 803px;
    background: var(--card);
    overflow: hidden;
  }
  .tag--front { left: 89px; }
  .tag--back  { left: 630px; }
  .punch-hole {
    position: absolute;
    top: 24px;
    left: 229px;
    width: 24px;
    height: 24px;
    border-radius: 50%;
    background: var(--hole);
    z-index: 3;
  }
  .tag--back .punch-hole { left: 228px; }
  .brand-mark {
    position: absolute;
    left: 166px;
    top: 418px;
    width: 150px;
    height: 150px;
    border-radius: 50%;
    background: linear-gradient(90deg, #c51b86 0%, var(--magenta) 100%);
  }
  .brand-name {
    position: absolute;
    left: 0;
    right: 0;
    top: 652px;
    margin: 0;
    text-align: center;
    font-family: "Quicksand", sans-serif;
    font-weight: 500;
    font-size: 76px;
    line-height: 1;
    letter-spacing: 0;
    color: var(--magenta);
  }
  .flow-pattern {
    position: absolute;
    left: 0;
    top: 100px;
    width: 482px;
    height: 620px;
    background:
      radial-gradient(ellipse at 85% 75%, rgba(228, 0, 109, 0.35), rgba(228, 0, 109, 0) 60%),
      linear-gradient(160deg, rgba(255,255,255,1) 15%, var(--rose-soft) 70%, rgba(228, 0, 109, 0.45) 100%);
  }
  .color-band {
    position: absolute;
    left: 0;
    bottom: 0;
    width: 482px;
    height: 85px;
    background: linear-gradient(90deg, var(--plum) 0%, #cc0f78 45%, var(--magenta) 100%);
  }
  .athletes-photo {
    position: absolute;
    left: 28px;
    top: 413px;
    width: 425px;
    height: 344px;
    border-radius: 40% 40% 8px 8px / 30% 30% 8px 8px;
    background: linear-gradient(135deg, var(--photo-mid) 0%, var(--photo-dark) 60%, #1a1a1a 100%);
    z-index: 2;
  }
</style>
</head>
<body>
<main class="sheet">
  <section class="tag tag--front" aria-label="Hang tag front">
    <span class="punch-hole"></span>
    <span class="brand-mark"></span>
    <p class="brand-name">Velora</p>
  </section>

  <section class="tag tag--back" aria-label="Hang tag back">
    <span class="punch-hole"></span>
    <div class="flow-pattern" role="img" aria-label="Flowing pink line pattern sweeping across the card"></div>
    <div class="color-band"></div>
    <div class="athletes-photo" role="img" aria-label="Photo of two young rhythmic gymnasts in black outfits stretching on the floor with arms raised"></div>
  </section>
</main>
</body>
</html>
```